Business Card Design

We are a manufacturing and distribution company with most of our customer base being supermarkets. We have established brand guidelines that are attached.

```html
<!DOCTYPE html>
<html lang="en">
<head>
<meta charset="utf-8">
<title>Veloria Business Card</title>
<link rel="stylesheet" href="https://fonts.googleapis.com/css2?family=Archivo+Black&family=Arimo:wght@400;700&display=swap">
<style>
  :root {
    --backdrop: #2b2b2b;
    --card-dark: #231f20;
    --card-light: #ffffff;
    --brand-red: #e31b23;
    --brand-blue: #006bb0;
    --ink: #1d1d1f;
    --wordmark-light: #e6e6e6;
  }
  * { box-sizing: border-box; margin: 0; padding: 0; }
  html, body { width: 1200px; height: 1015px; overflow: hidden; }
  body {
    background: var(--backdrop);
    font-family: "Arimo", Arial, sans-serif;
    position: relative;
  }
  .card {
    position: absolute;
    left: 250px;
    width: 700px;
    height: 400px;
    box-shadow: 0 12px 30px rgba(0,0,0,.45);
  }
  /* Back side */
  .card-back {
    top: 60px;
    background: var(--card-dark);
    display: flex;
    align-items: center;
    justify-content: center;
    gap: 22px;
  }
  .card-back .brand-square {
    width: 34px; height: 34px;
    background: var(--brand-red);
  }
  .card-back .brand-name {
    font-family: "Archivo Black", Arial, sans-serif;
    font-size: 58px;
    letter-spacing: 4px;
    color: var(--wordmark-light);
  }
  /* Front side */
  .card-front {
    top: 555px;
    background: var(--card-light);
  }
  .holder {
    position: absolute;
    left: 0; top: 150px;
    display: flex;
    align-items: center;
  }
  .holder .accent {
    width: 56px; height: 44px;
    background: var(--brand-red);
    margin-right: 18px;
  }
  .holder-name {
    font-family: "Archivo Black", Arial, sans-serif;
    font-size: 25px;
    color: var(--ink);
    letter-spacing: .5px;
    line-height: 1;
  }
  .holder-title {
    font-size: 15px;
    color: var(--ink);
    letter-spacing: 1px;
    margin-top: 4px;
  }
  .contacts {
    position: absolute;
    left: 74px; top: 228px;
    list-style: none;
  }
  .contacts li {
    display: flex;
    align-items: center;
    gap: 10px;
    font-size: 17px;
    color: var(--ink);
    line-height: 26px;
  }
  .contacts svg { width: 16px; height: 16px; fill: var(--brand-red); flex: none; }
  .address {
    position: absolute;
    left: 100px; top: 330px;
    font-size: 17px;
    line-height: 24px;
    color: var(--ink);
  }
  .front-brand {
    position: absolute;
    right: 50px; top: 60px;
    display: flex;
    align-items: center;
    gap: 16px;
  }
  .front-brand .brand-square {
    width: 40px; height: 40px;
    background: var(--brand-red);
  }
  .front-brand .brand-name {
    font-family: "Archivo Black", Arial, sans-serif;
    font-size: 52px;
    letter-spacing: 3px;
    color: var(--brand-blue);
  }
</style>
</head>
<body>
  <section class="card card-back">
    <span class="brand-square"></span>
    <span class="brand-name">VELORIA</span>
  </section>

  <section class="card card-front">
    <div class="front-brand">
      <span class="brand-square"></span>
      <span class="brand-name">VELORIA</span>
    </div>

    <div class="holder">
      <span class="accent"></span>
      <div>
        <p class="holder-name">DANIEL HARTLEY</p>
        <p class="holder-title">MANAGING DIRECTOR</p>
      </div>
    </div>

    <ul class="contacts">
      <li>
        <svg viewBox="0 0 24 24" aria-hidden="true"><path d="M6.6 10.8a15.1 15.1 0 0 0 6.6 6.6l2.2-2.2c.3-.3.7-.4 1-.2 1.1.4 2.3.6 3.6.6.6 0 1 .4 1 1V20c0 .6-.4 1-1 1A17 17 0 0 1 3 4c0-.6.4-1 1-1h3.5c.6 0 1 .4 1 1 0 1.3.2 2.5.6 3.6.1.3 0 .7-.2 1z"/></svg>
        044-987 650 321
      </li>
      <li>
        <svg viewBox="0 0 24 24" aria-hidden="true"><path d="M2 5h20v14H2z" fill="none"/><path d="M2 5h20v2l-10 6L2 7zM2 9l10 6 10-6v10H2z"/></svg>
        hello@veloria.com
      </li>
      <li>
        <svg viewBox="0 0 24 24" aria-hidden="true"><path d="M12 2a10 10 0 1 0 0 20 10 10 0 0 0 0-20zm6.9 6h-3a15 15 0 0 0-1.3-3.9A8 8 0 0 1 18.9 8zM12 4c.8 1.2 1.5 2.5 1.9 4h-3.8c.4-1.5 1.1-2.8 1.9-4zM4.3 14a8 8 0 0 1 0-4h3.4a16 16 0 0 0 0 4zm.8 2h3a15 15 0 0 0 1.3 3.9A8 8 0 0 1 5.1 16zm3-8h-3a8 8 0 0 1 4.3-3.9A15 15 0 0 0 8.1 8zM12 20c-.8-1.2-1.5-2.5-1.9-4h3.8c-.4 1.5-1.1 2.8-1.9 4zm2.3-6H9.7a14 14 0 0 1 0-4h4.6a14 14 0 0 1 0 4zm.3 5.9a15 15 0 0 0 1.3-3.9h3a8 8 0 0 1-4.3 3.9zm1.7-5.9a16 16 0 0 0 0-4h3.4a8 8 0 0 1 0 4z"/></svg>
        www.veloriagoods.com
      </li>
    </ul>

    <p class="address">421, Address line goes here<br>45452, Country Name</p>
  </section>
</body>
</html>
```